Professional, modern and unique business card. We are looking to present a new look to our business cards however we don't want to divert too far away from original template. We want social media links and our 3 office addresses on the backside of the business cards. Please see attached business card templates for ideas.
Crestline Homes Color Code:
R: 7
G:63
B:86

Target Market(s)

Real Estate

Industry/Entity Type

Real Estate

Contact Information for Business Card

Follow the attached templates. In need of a more modern and unique touch but don't want to divert from the original theme or color.
Crestline Homes Color Code:
R: 7
G:63
B:86

Font styles to use
Serif

Requirements
Must have
• Crestline Homes logo, Crestline homes colors, social media links, 3 office addresses,
Nice to have
• information about Crestline Homes and QR codes. You can check out www.mycrestlinehomes.example

```html
<!DOCTYPE html>
<html lang="en">
<head>
<meta charset="utf-8">
<title>Crestline Homes Business Card</title>
<link rel="stylesheet" href="https://fonts.googleapis.com/css2?family=Lato:wght@400;700&display=swap">
<style>
  :root {
    --backdrop: #5b5b5b;
    --card-blue: #0e7ab5;
    --card-white: #ffffff;
    --ink: #333333;
    --ink-white: #ffffff;
    --logo-tint: #e6f1f7;
    --rule-light: #dddddd;
    --rule-blue: rgba(255,255,255,0.35);
    --dot-blue: #3b5998;
    --dot-red: #cc2127;
    --dot-navy: #0e5e96;
    --dot-sky: #1da1f2;
  }
  * { margin: 0; padding: 0; box-sizing: border-box; }
  html, body { width: 1200px; height: 900px; overflow: hidden; }
  body {
    position: relative;
    background: var(--backdrop);
    font-family: "Lato", sans-serif;
  }
  .card {
    position: absolute;
    top: 275px;
    width: 477px;
    height: 292px;
    box-shadow: 3px 4px 6px rgba(0,0,0,0.55);
  }
  .card-front {
    left: 120px;
    background: var(--card-blue);
    border-radius: 0 62px 0 62px;
    color: var(--ink-white);
  }
  .card-back {
    left: 606px;
    background: var(--card-white);
    border-radius: 62px 0 62px 0;
    color: var(--ink);
  }
  .brand {
    position: absolute;
    left: 30px;
    top: 118px;
    width: 200px;
    text-align: center;
    font-family: "Lato", sans-serif;
    font-weight: 700;
    font-size: 26px;
    line-height: 30px;
    color: var(--logo-tint);
    letter-spacing: 1px;
  }
  .brand-divider {
    position: absolute;
    left: 238px;
    top: 70px;
    width: 1px;
    height: 145px;
    background: var(--rule-blue);
  }
  .person {
    position: absolute;
    left: 256px;
    top: 78px;
  }
  .person-name {
    font-weight: 700;
    font-size: 19px;
    line-height: 22px;
    text-transform: uppercase;
  }
  .person-title {
    font-size: 14px;
    line-height: 17px;
    text-transform: uppercase;
  }
  .contact-list {
    position: absolute;
    left: 256px;
    top: 133px;
    list-style: none;
  }
  .contact-list li {
    display: flex;
    align-items: center;
    font-size: 14px;
    line-height: 16.4px;
  }
  .contact-list svg { width: 10px; height: 10px; margin-right: 5px; fill: var(--ink-white); }
  .office-list {
    position: absolute;
    left: 0;
    top: 82px;
    width: 100%;
    text-align: center;
    list-style: none;
    font-size: 14px;
    line-height: 23px;
  }
  .back-rule {
    position: absolute;
    left: 32px;
    top: 168px;
    width: 412px;
    height: 1px;
    background: var(--rule-light);
  }
  .social-row {
    position: absolute;
    left: 14px;
    width: 449px;
    display: flex;
    justify-content: space-between;
    gap: 10px;
    font-size: 12px;
  }
  .social-row.first { top: 183px; }
  .social-row.second { top: 215px; }
  .social-item { display: flex; align-items: center; white-space: nowrap; }
  .social-dot {
    width: 18px; height: 18px; border-radius: 50%;
    margin-right: 4px; flex: none;
  }
  .dot-blue { background: var(--dot-blue); }
  .dot-red { background: var(--dot-red); }
  .dot-navy { background: var(--dot-navy); }
  .dot-sky { background: var(--dot-sky); }
</style>
</head>
<body>
  <section class="card card-front">
    <div class="brand">Crestline Homes</div>
    <div class="brand-divider"></div>
    <div class="person">
      <div class="person-name">Dana Whitfield</div>
      <div class="person-title">Managing Director</div>
    </div>
    <ul class="contact-list">
      <li><svg viewBox="0 0 10 10"><path d="M1 3 Q5 0 9 3 L8 4.5 L6.5 3.8 L6.5 3 Q5 2.6 3.5 3 L3.5 3.8 L2 4.5 Z M2.5 5 H7.5 L8.5 9 H1.5 Z"/></svg>410 555 0128</li>
      <li><svg viewBox="0 0 10 10"><path d="M3 0 H7 Q8 0 8 1 V9 Q8 10 7 10 H3 Q2 10 2 9 V1 Q2 0 3 0 Z M3 1.5 V7.5 H7 V1.5 Z"/></svg>410 555 0173</li>
      <li><svg viewBox="0 0 10 10"><path d="M2.5 0 H7.5 V3 H2.5 Z M0 3.5 H10 V7.5 H8 V10 H2 V7.5 H0 Z M3 6.5 V9 H7 V6.5 Z"/></svg>410 555 0190</li>
      <li><svg viewBox="0 0 10 10"><path d="M0 2 H10 V8.5 H0 Z M1 3 L5 6 L9 3 Z" fill-rule="evenodd"/></svg>hello@crestline.example</li>
      <li><svg viewBox="0 0 10 10"><circle cx="5" cy="5" r="5"/><path d="M5 0.8 Q2.5 5 5 9.2 M5 0.8 Q7.5 5 5 9.2 M0.8 5 H9.2" stroke="#0e7ab5" stroke-width="0.8" fill="none"/></svg>www.crestline.example</li>
    </ul>
  </section>

  <section class="card card-back">
    <ul class="office-list">
      <li>1420 Harbor Ave Brooklyn, NY 11209</li>
      <li>72-18 Maple Blvd Kew Gardens, NY 11415</li>
      <li>318-04 Orchard Blvd Little Neck, NY 11362</li>
    </ul>
    <div class="back-rule"></div>
    <div class="social-row first">
      <span class="social-item"><span class="social-dot dot-blue"></span>CrestlinehomesNY</span>
      <span class="social-item"><span class="social-dot dot-red"></span>Info at Crestline Homes</span>
      <span class="social-item"><span class="social-dot dot-navy"></span>@CrestlineHomesNY</span>
    </div>
    <div class="social-row second">
      <span class="social-item"><span class="social-dot dot-red"></span>Crestline Homes</span>
      <span class="social-item"><span class="social-dot dot-navy"></span>Crestline Homes New York</span>
      <span class="social-item"><span class="social-dot dot-sky"></span>@CrestlineHomesQ</span>
    </div>
  </section>
</body>
</html>
```